Tall fern bicycle rental

would like to have a bicycle rental website that has the ability to have a calender and be able to sign a liability waiver and pay all on line, We rent fat tire vorn bicycles

```html
<!DOCTYPE html>
<html lang="en">
<head>
<meta charset="utf-8">
<title>Tall Fern Bicycle Rental</title>
<link href="https://fonts.googleapis.com/css2?family=Roboto:wght@400;500;700;900&display=swap" rel="stylesheet">
<style>
:root{
  --blue:#1e8bcf;
  --blue-deep:#0e6fb4;
  --band:#1a7fc4;
  --ink:#1c1c1c;
  --muted:#8a8a8a;
  --soft:#f1f1f1;
  --line:#e3e3e3;
  --red:#c8102e;
  --white:#ffffff;
  --black:#050505;
}
*{box-sizing:border-box;margin:0;padding:0}
html,body{width:1200px;height:4089px;overflow:hidden}
body{position:relative;background:var(--white);font-family:"Roboto",Arial,sans-serif;color:var(--ink)}
.abs{position:absolute}
a{color:inherit;text-decoration:none}

/* header */
.site-header{position:absolute;left:0;top:0;width:1200px;height:102px;background:var(--white);border-top:3px solid var(--blue);z-index:5}
.brand-tab{position:absolute;left:88px;top:-60px;width:190px;height:235px;border-radius:0 0 95px 95px;background:var(--white);z-index:6;display:flex;align-items:flex-end;justify-content:center;padding-bottom:58px}
.brand-name{font-weight:700;font-size:19px;line-height:1.15;color:var(--blue-deep);text-align:center;text-transform:uppercase;width:150px}
.main-nav{position:absolute;left:400px;top:40px;display:flex;gap:29px;font-size:13.5px;font-weight:500;letter-spacing:.2px}
.main-nav a.active{color:var(--blue)}
.nav-caret{position:absolute;left:415px;top:0;width:0;height:0;border-left:7px solid transparent;border-right:7px solid transparent;border-top:7px solid var(--blue)}
.login-btn{position:absolute;left:951px;top:24px;width:136px;height:49px;border-radius:25px;background:var(--blue);color:var(--white);font-size:14px;font-weight:700;display:flex;align-items:center;justify-content:center;gap:8px}

/* hero */
.hero{position:absolute;left:0;top:102px;width:1200px;height:509px;overflow:hidden}
.hero-photo{position:absolute;inset:0;background:linear-gradient(120deg,#3f6a86 0%,#7fa3b8 35%,#a9bfcc 55%,#c9d6de 100%)}
.hero-title{position:absolute;left:705px;top:165px;font-size:52px;font-weight:900;line-height:60px;color:var(--white);text-transform:uppercase}
.hero-btn{position:absolute;left:705px;top:301px;width:125px;height:30px;border-radius:15px;background:var(--white);color:var(--blue-deep);font-size:14px;font-weight:700;display:flex;align-items:center;justify-content:center}

/* quick search */
.quick-search{position:absolute;left:111px;top:651px;width:978px;height:179px;background:#efefef;border-bottom:4px solid var(--blue)}
.qs-title{position:absolute;left:37px;top:50px;font-size:33px;font-weight:900;line-height:41px}
.calendar{position:absolute;left:200px;top:9px;width:145px;height:157px;background:var(--white)}
.cal-head{height:40px;background:var(--red);color:var(--white);font-weight:700;font-size:16px;display:flex;justify-content:space-between;align-items:center;padding:0 10px}
.cal-grid{display:grid;grid-template-columns:repeat(7,1fr);padding:6px 6px 0;font-size:8px;text-align:center;row-gap:5px}
.cal-grid .dow{font-size:5px;color:#777}
.cal-grid .today{background:var(--red);color:var(--white)}
.date-field{position:absolute;top:49px;width:215px}
.date-label{font-size:13px;font-weight:700;color:#444}
.date-input{margin-top:26px;height:30px;border-bottom:2px solid #b7b7b7;font-size:13px;color:#b0b0b0;display:flex;justify-content:space-between;align-items:center;padding:0 11px}
.search-btn{position:absolute;left:888px;top:80px;width:42px;height:42px;border-radius:50%;background:var(--blue-deep);display:flex;align-items:center;justify-content:center}

/* easy rental */
.map-visual{position:absolute;left:48px;top:913px;width:555px;height:436px;background:radial-gradient(ellipse at 50% 45%,#e6ecf1 0%,#f0f2f4 55%,#ffffff 100%)}
.section-heading{font-weight:900;font-size:35px;text-transform:uppercase;color:var(--ink)}
.easy-title{position:absolute;left:625px;top:925px}
.easy-text{position:absolute;left:626px;top:996px;width:510px;font-size:13.5px;line-height:26px;color:var(--muted)}
.feature{position:absolute;left:627px;display:flex;align-items:center;gap:28px;font-size:14px;color:#555}
.feature-icon{width:66px;height:66px;border-radius:50%;border:2px solid var(--blue);display:flex;align-items:center;justify-content:center}

/* pricing band */
.pricing{position:absolute;left:0;top:1405px;width:1200px;height:431px;background:linear-gradient(180deg,#1976b9 0%,#1f88cc 60%,#2a8fcf 100%)}
.pricing-photo{position:absolute;left:430px;top:0;width:380px;height:431px;background:radial-gradient(ellipse at 50% 40%,rgba(20,50,80,.35),rgba(20,50,80,0) 70%)}
.pricing-title{position:absolute;left:0;top:93px;width:1200px;text-align:center;font-size:35px;font-weight:900;color:var(--white)}
.perk{position:absolute;top:165px;width:130px;text-align:center;color:var(--white);font-weight:700;font-size:17px}
.perk-circle{width:130px;height:130px;border-radius:50%;background:var(--white);display:flex;align-items:center;justify-content:center;margin-bottom:20px}

/* why choose */
.why-title{position:absolute;left:0;top:1930px;width:1200px;text-align:center}
.why-photo{position:absolute;left:457px;top:2057px;width:282px;height:282px;border-radius:50%;background:radial-gradient(circle at 60% 40%,#f2d9a7 0%,#c9a173 40%,#6f6a5e 100%)}
.why-item{position:absolute;width:300px}
.why-item h3{font-size:19px;font-weight:700;line-height:26px;color:var(--blue-deep)}
.why-item p{margin-top:18px;font-size:13.5px;line-height:26px;color:var(--muted)}
.why-item.left{text-align:right}

/* fleet */
.fleet{position:absolute;left:0;top:2471px;width:1200px;height:507px;background:var(--soft)}
.fleet-title{position:absolute;left:0;top:95px;width:1200px;text-align:center}
.bike-card{position:absolute;top:173px;width:283px;height:232px;background:linear-gradient(180deg,#ffffff 0%,#eeeeee 100%)}
.bike-card.featured{background:linear-gradient(180deg,#f7f7f7 0%,#7a8a6a 75%,#6a7c57 100%)}
.bike-overlay{position:absolute;left:11px;top:10px;width:258px;height:222px;background:rgba(34,70,110,.72);color:var(--white);text-align:center;font-weight:700;font-size:18px;line-height:31px;padding-top:53px}
.book-btn{display:inline-block;margin-top:10px;width:124px;height:38px;line-height:38px;border-radius:19px;background:var(--blue);font-size:14px}

/* news */
.news-title{position:absolute;left:0;top:3073px;width:1200px;text-align:center}
.news-card{position:absolute;top:3152px;width:396px}
.news-photo{height:283px;position:relative}
.news-photo.one{background:linear-gradient(180deg,#b7cf5a 0%,#6f9a2e 60%,#d9dbd2 100%)}
.news-photo.two{background:linear-gradient(180deg,#e8e4dc 0%,#b9a98f 50%,#5c5c5c 100%)}
.news-date{position:absolute;left:0;bottom:0;width:150px;height:34px;background:var(--white);font-size:13px;font-weight:700;display:flex;align-items:center;justify-content:center;gap:6px}
.news-card h3{margin-top:34px;font-size:19px;font-weight:700}
.news-card p{margin-top:8px;font-size:13.5px;line-height:25px;color:var(--muted)}
.read-btn{display:inline-flex;align-items:center;justify-content:center;gap:5px;margin-top:22px;width:131px;height:43px;border-radius:22px;background:var(--blue);color:var(--white);font-size:14px;font-weight:700}
.arrow{position:absolute;top:3350px}

/* footer */
.site-footer{position:absolute;left:0;top:3716px;width:1200px;height:373px;background:var(--black);color:var(--white)}
.footer-brand{position:absolute;left:111px;top:70px;width:250px;display:flex;flex-direction:column;align-items:center;gap:14px}
.footer-mark{width:124px;height:124px;border-radius:50%;background:var(--white)}
.footer-name{font-size:24px;font-weight:700;text-transform:uppercase;text-align:center;line-height:28px}
.footer-col{position:absolute;top:78px}
.footer-col h4{font-size:21px;font-weight:700;padding-bottom:12px;border-bottom:2px solid var(--blue);width:150px}
.footer-col ul{list-style:none;margin-top:26px;font-size:14px;line-height:26px}
.footer-col p{margin-top:26px;font-size:14px;line-height:26px;width:240px}
.subscribe{margin-top:18px;display:flex;width:235px;height:35px;border:1px solid #fff}
.subscribe span{flex:1;background:var(--white);color:#999;font-size:11px;padding:11px 16px}
.subscribe b{width:68px;background:var(--blue);font-size:12px;display:flex;align-items:center;justify-content:center}
.footer-rule{position:absolute;left:111px;top:304px;width:978px;height:1px;background:#333}
.follow{position:absolute;left:110px;top:326px;display:flex;align-items:center;gap:15px;font-size:14px}
.social{width:28px;height:28px;border-radius:50%;background:var(--blue)}
.copyright{position:absolute;right:113px;top:332px;font-size:14px}
</style>
</head>
<body>

<header class="site-header">
  <div class="nav-caret"></div>
  <nav class="main-nav">
    <a class="active" href="#">HOME</a><a href="#">ABOUT</a><a href="#">SERVICES</a><a href="#">BICYCLES</a><a href="#">BLOG</a><a href="#">CONTACT US</a>
  </nav>
  <a class="login-btn" href="#">
    <svg width="15" height="15" viewBox="0 0 16 16" fill="none" stroke="#fff" stroke-width="1.6"><circle cx="8" cy="8" r="7"/><circle cx="8" cy="6.3" r="2.4"/><path d="M3.5 13c1-2 2.6-3 4.5-3s3.5 1 4.5 3"/></svg>
    LOG IN
  </a>
</header>
<div class="brand-tab"><span class="brand-name">Tall Fern Bicycle Rental</span></div>

<section class="hero">
  <div class="hero-photo" role="img" aria-label="Road cyclist in a helmet riding a blue racing bike downhill"></div>
  <svg class="abs" style="left:0;top:0" width="1200" height="509">
    <polygon points="640,0 1200,0 1200,509 420,509" fill="#1f88cc" opacity=".55"/>
    <polygon points="760,0 1200,0 1200,509 600,509" fill="#1c82c6" opacity=".45"/>
    <polygon points="1060,0 1200,0 1200,509 900,509" fill="#ffffff" opacity=".12"/>
  </svg>
  <h1 class="hero-title">Rent a bike<br>you love</h1>
  <a class="hero-btn" href="#">Find a Bicycle</a>
</section>

<section class="quick-search">
  <h2 class="qs-title">QUICK<br>SEARCH</h2>
  <div class="calendar">
    <div class="cal-head"><span>MAY</span><span>2020</span></div>
    <div class="cal-grid">
      <span class="dow">SUN</span><span class="dow">MON</span><span class="dow">TUE</span><span class="dow">WED</span><span class="dow">THU</span><span class="dow">FRI</span><span class="dow">SAT</span>
      <span></span><span></span><span></span><span></span><span></span><span>1</span><span>2</span>
      <span>3</span><span>4</span><span>5</span><span>6</span><span>7</span><span>8</span><span>9</span>
      <span>10</span><span>11</span><span>12</span><span>13</span><span>14</span><span>15</span><span>16</span>
      <span>17</span><span>18</span><span class="today">19</span><span>20</span><span>21</span><span>22</span><span>23</span>
      <span>24</span><span>25</span><span>26</span><span>27</span><span>28</span><span>29</span><span>30</span>
    </div>
  </div>
  <div class="date-field" style="left:381px">
    <div class="date-label">PICKUP DATE</div>
    <div class="date-input"><span>05/19/2020</span><svg width="12" height="12" viewBox="0 0 12 12"><rect x="1" y="2" width="10" height="9" fill="none" stroke="#1e8bcf"/><rect x="1" y="2" width="10" height="3" fill="#1e8bcf"/></svg></div>
  </div>
  <div class="date-field" style="left:638px">
    <div class="date-label">RETURN DATE</div>
    <div class="date-input"><span>05/20/2020</span><svg width="12" height="12" viewBox="0 0 12 12"><rect x="1" y="2" width="10" height="9" fill="none" stroke="#1e8bcf"/><rect x="1" y="2" width="10" height="3" fill="#1e8bcf"/></svg></div>
  </div>
  <div class="search-btn"><svg width="14" height="14" viewBox="0 0 14 14" fill="none" stroke="#fff" stroke-width="2"><circle cx="6" cy="6" r="4"/><path d="M9 9l3.5 3.5"/></svg></div>
</section>

<div class="map-visual" role="img" aria-label="World map with a smartphone showing a rental route between two streets"></div>
<h2 class="section-heading easy-title">Easy bicycle rental service</h2>
<p class="easy-text">Lorem ipsum dolor sit amet, consectetur adipiscing elit, sed do eiusmod tem por incididunt ut labore et dolore magna aliqua. Ut enim ad minim veniam, quis nostrud exercitation ullamco laboris nisi ut aliquip</p>
<div class="feature" style="top:1083px">
  <div class="feature-icon"><svg width="36" height="36" viewBox="0 0 36 36" fill="none" stroke="#1e8bcf" stroke-width="2.4"><circle cx="18" cy="18" r="14"/><path d="M8 28L28 8"/></svg></div>
  <span>Free booking cancellation up to 15 hours</span>
</div>
<div class="feature" style="top:1159px">
  <div class="feature-icon"><svg width="36" height="36" viewBox="0 0 36 36" fill="none" stroke="#1e8bcf" stroke-width="2"><circle cx="18" cy="18" r="13"/><circle cx="18" cy="18" r="10" stroke-dasharray="2 3"/><path d="M18 11v7l5 3"/></svg></div>
  <span>We offer 24/7 road rental assistance</span>
</div>
<div class="feature" style="top:1235px">
  <div class="feature-icon"><svg width="36" height="36" viewBox="0 0 36 36" fill="none" stroke="#1e8bcf" stroke-width="2"><circle cx="18" cy="13" r="6"/><path d="M9 13a9 9 0 0118 0"/><path d="M7 32c1-6 5-9 11-9s10 3 11 9z"/></svg></div>
  <span>More than 350.000 satisfied customers</span>
</div>

<section class="pricing">
  <div class="pricing-photo" role="img" aria-label="Faded cyclist in a helmet behind the blue band"></div>
  <h2 class="pricing-title">OUR PRICING INCLUDES</h2>
  <div class="perk" style="left:143px"><div class="perk-circle"><svg width="72" height="72" viewBox="0 0 72 72" fill="none" stroke="#111" stroke-width="3.5" stroke-linejoin="round"><path d="M10 44c0-18 12-30 28-30 14 0 24 10 24 24 0 8-3 14-6 18H16c-4 0-6-4-6-12z"/><path d="M30 30h26l6 8H34z"/><path d="M16 56l8-10h32"/></svg></div>Helmets</div>
  <div class="perk" style="left:338px"><div class="perk-circle"><svg width="72" height="72" viewBox="0 0 72 72" fill="none" stroke="#111" stroke-width="3.5"><path d="M14 44V36a22 22 0 0144 0v8"/><rect x="12" y="42" width="10" height="18" rx="4"/><rect x="50" y="42" width="10" height="18" rx="4"/></svg></div>Helmets</div>
  <div class="perk" style="left:533px"><div class="perk-circle"><svg width="72" height="72" viewBox="0 0 72 72" fill="none" stroke="#111" stroke-width="3"><path d="M18 12h28v48H18z"/><path d="M24 22h16M24 30h16M24 38h10"/><path d="M44 38l12 4v8c0 6-5 10-12 12-7-2-12-6-12-12v-8z" fill="#fff"/><path d="M39 50l4 4 7-8"/></svg></div>Helmets</div>
  <div class="perk" style="left:729px"><div class="perk-circle"><svg width="72" height="72" viewBox="0 0 72 72" fill="none" stroke="#111" stroke-width="3.5"><path d="M36 8l6 6h8v8l6 6-6 6v8h-8l-6 6-6-6h-8v-8l-6-6 6-6v-8h8z" transform="translate(0 8)"/><circle cx="30" cy="30" r="3"/><circle cx="42" cy="42" r="3"/><path d="M28 44l16-16"/></svg></div>Helmets</div>
  <div class="perk" style="left:924px"><div class="perk-circle"><svg width="72" height="72" viewBox="0 0 72 72" fill="none" stroke="#111" stroke-width="3.5"><circle cx="36" cy="36" r="28"/><path d="M24 24l24 24M48 24L24 48"/></svg></div>Helmets</div>
</section>

<h2 class="section-heading why-title">WHY CHOOSE TALL FERN BICYCLE RENTAL</h2>
<svg class="abs" style="left:428px;top:2028px" width="340" height="340">
  <circle cx="170" cy="170" r="167" fill="none" stroke="#222" stroke-width="3" stroke-dasharray="0.1 13" stroke-linecap="round"/>
  <circle cx="43" cy="69" r="9" fill="#1e8bcf"/><circle cx="301" cy="69" r="9" fill="#1e8bcf"/>
  <circle cx="43" cy="275" r="9" fill="#1e8bcf"/><circle cx="301" cy="275" r="9" fill="#1e8bcf"/>
</svg>
<div class="why-photo" role="img" aria-label="Cyclist wearing a mask riding through a sunlit street"></div>
<div class="why-item left" style="left:83px;top:2047px"><h3>Fully Insured<br>Rental Service</h3><p>Lorem ipsum dolor sit amet, conse ctetur adipiscing elit, sed do</p></div>
<div class="why-item left" style="left:83px;top:2255px"><h3>We rent fat tire<br>vorn bicycles</h3><p>Lorem ipsum dolor sit amet, conse ctetur adipiscing elit, sed do</p></div>
<div class="why-item" style="left:817px;top:2047px"><h3>Smart Mobility<br>for Clients</h3><p>Lorem ipsum dolor sit amet, conse ctetur adipiscing elit, sed do</p></div>
<div class="why-item" style="left:817px;top:2255px"><h3>Designed for<br>Modern World</h3><p>Lorem ipsum dolor sit amet, conse ctetur adipiscing elit, sed do</p></div>

<section class="fleet">
  <h2 class="section-heading fleet-title">OUR RENTING FLEET</h2>
  <div class="bike-card" style="left:0" role="img" aria-label="Black mountain bike with red accents"></div>
  <div class="bike-card featured" style="left:306px" role="img" aria-label="Bicycle lifted overhead in a park">
    <div class="bike-overlay">Model 2020<br>Lorem ipsum dolor<br>Rent $20.00<br><span class="book-btn">BOOK NOW</span></div>
  </div>
  <div class="bike-card" style="left:611px" role="img" aria-label="Orange mountain bike"></div>
  <div class="bike-card" style="left:917px" role="img" aria-label="White and yellow mountain bike"></div>
</section>

<h2 class="section-heading news-title">OUR LATEST NEWS</h2>
<svg class="arrow" style="left:93px" width="34" height="18" viewBox="0 0 34 18" fill="none" stroke="#bbb" stroke-width="3"><path d="M33 9H3M10 2L3 9l7 7"/></svg>
<svg class="arrow" style="left:1072px" width="34" height="18" viewBox="0 0 34 18" fill="none" stroke="#bbb" stroke-width="3"><path d="M1 9h30M24 2l7 7-7 7"/></svg>
<article class="news-card" style="left:182px">
  <div class="news-photo one" role="img" aria-label="Man in a mask cycling on a park path">
    <div class="news-date"><svg width="12" height="12" viewBox="0 0 12 12"><rect x="1" y="2" width="10" height="9" fill="none" stroke="#333"/><rect x="1" y="2" width="10" height="3" fill="#333"/></svg>JAN 25,2020</div>
  </div>
  <h3>Lorem ipsum dolor sit amet, consectetur</h3>
  <p>Lorem ipsum dolor sit amet, consectetur adipiscing elit, sed do eiusmod tempor incididunt ut labore</p>
  <a class="read-btn" href="#">Read more <svg width="12" height="12" viewBox="0 0 12 12"><circle cx="6" cy="6" r="6" fill="#fff"/><path d="M5 3.5L7.5 6 5 8.5" stroke="#1e8bcf" stroke-width="1.6" fill="none"/></svg></a>
</article>
<article class="news-card" style="left:617px">
  <div class="news-photo two" role="img" aria-label="Road cyclist riding at sunset">
    <div class="news-date"><svg width="12" height="12" viewBox="0 0 12 12"><rect x="1" y="2" width="10" height="9" fill="none" stroke="#333"/><rect x="1" y="2" width="10" height="3" fill="#333"/></svg>JAN 25,2020</div>
  </div>
  <h3>Lorem ipsum dolor sit amet, consectetur</h3>
  <p>Lorem ipsum dolor sit amet, consectetur adipiscing elit, sed do eiusmod tempor incididunt ut labore</p>
  <a class="read-btn" href="#">Read more <svg width="12" height="12" viewBox="0 0 12 12"><circle cx="6" cy="6" r="6" fill="#fff"/><path d="M5 3.5L7.5 6 5 8.5" stroke="#1e8bcf" stroke-width="1.6" fill="none"/></svg></a>
</article>

<footer class="site-footer">
  <div class="footer-brand">
    <div class="footer-mark"></div>
    <div class="footer-name">Tall Fern Bicycle Rental</div>
  </div>
  <div class="footer-col" style="left:441px"><h4>Sitelinks</h4><ul><li>Home</li><li>About us</li><li>Services</li><li>Blog</li><li>Contact us</li></ul></div>
  <div class="footer-col" style="left:630px"><h4>Info</h4><ul><li>Privacy policy</li><li>Support</li><li>Terms &amp; Condition</li><li>Customer Support</li><li>Team</li></ul></div>
  <div class="footer-col" style="left:852px"><h4>Stay in Touch</h4><p>Lorem ipsum dolor sit amet, consect etur adipiscing</p><div class="subscribe"><span>Email</span><b>SUBMIT</b></div></div>
  <div class="footer-rule"></div>
  <div class="follow">Follow us :<span class="social"></span><span class="social"></span><span class="social"></span><span class="social"></span></div>
  <div class="copyright">© Copyrights 2020 Tall Fern Bicycle Rental | All Right Reserved</div>
</footer>

</body>
</html>
```